velmora - business cards

Need business card designs - logo provided - see www.velmora.co.nz

Industry/Entity Type

Business

Requirements
Must have
• logo - provided in attachments
• www.velmora.co.nz

```html
<!DOCTYPE html>
<html lang="en">
<head>
<meta charset="utf-8">
<title>velmora – business cards</title>
<link rel="stylesheet" href="https://fonts.googleapis.com/css2?family=Arimo:wght@400;700&display=swap">
<style>
  :root {
    --stage: #ecebe8;
    --card-dark: #333333;
    --card-light: #e4e4e4;
    --ink: #3a3a3a;
    --ink-soft: #555555;
    --brand-blue: #1f78b4;
    --wordmark-light: #dcdcdc;
    --accent-orange: #e8772e;
  }
  * { box-sizing: border-box; margin: 0; padding: 0; }
  html, body {
    width: 1200px; height: 900px; overflow: hidden;
    background: var(--stage);
    font-family: "Arimo", Arial, sans-serif;
  }
  .stage {
    position: relative; width: 1200px; height: 900px;
    display: flex; align-items: center; justify-content: center; gap: 40px;
  }
  .card {
    position: relative; width: 520px; height: 297px;
    box-shadow: 0 6px 18px rgba(0,0,0,0.18);
    overflow: hidden;
  }
  /* Front */
  .card-front {
    background: var(--card-dark);
    display: flex; align-items: center; justify-content: center; gap: 16px;
  }
  .brand-dot {
    width: 40px; height: 40px; border-radius: 50%;
    background: var(--brand-blue);
  }
  .wordmark {
    font-weight: 700; font-size: 62px; letter-spacing: 1px;
    color: var(--wordmark-light); line-height: 1;
  }
  /* Back */
  .card-back {
    background: var(--card-light);
    color: var(--ink);
    padding: 34px 0 0 36px;
  }
  .brand-corner {
    position: absolute; top: 30px; right: 34px;
    display: flex; align-items: center; gap: 8px;
  }
  .brand-corner .brand-dot { width: 18px; height: 18px; }
  .brand-corner .wordmark {
    font-size: 24px; color: var(--brand-blue);
  }
  .holder { display: flex; align-items: baseline; gap: 8px; margin-bottom: 10px; }
  .holder-name { font-size: 21px; font-weight: 400; color: var(--ink); }
  .holder-role { font-size: 10px; letter-spacing: 0.4px; color: var(--ink-soft); text-transform: uppercase; }
  .contact-list { list-style: none; font-size: 11.5px; line-height: 1.55; }
  .contact-list li { position: relative; padding-left: 16px; }
  .contact-list li::before {
    content: ""; position: absolute; left: 2px; top: 5px;
    border-left: 6px solid var(--accent-orange);
    border-top: 4px solid transparent; border-bottom: 4px solid transparent;
  }
  .contact-list strong { font-weight: 700; }
  .web {
    position: absolute; left: 36px; bottom: 42px;
    font-size: 13px; color: var(--ink);
    padding-top: 5px; border-top: 1.5px solid var(--accent-orange);
    width: 118px;
  }
  .web b { color: var(--accent-orange); font-weight: 700; }
  .base-band {
    position: absolute; left: 0; right: 0; bottom: 0; height: 20px;
    background: var(--card-dark);
  }
</style>
</head>
<body>
  <main class="stage">
    <section class="card card-front" aria-label="Business card front">
      <span class="brand-dot"></span>
      <span class="wordmark">velmora</span>
    </section>

    <section class="card card-back" aria-label="Business card back">
      <div class="brand-corner">
        <span class="brand-dot"></span>
        <span class="wordmark">velmora</span>
      </div>
      <div class="holder">
        <span class="holder-name">Elise Marren</span>
        <span class="holder-role">Operation Manager</span>
      </div>
      <ul class="contact-list">
        <li><strong>International:</strong> +64 21 480 336</li>
        <li><strong>Phone NZ:</strong> 0800 4 VELMO (0800 48-35-66)</li>
        <li><strong>Email:</strong> info@velmora.co.nz</li>
        <li>P.O.Box 204873,<br>Auckland, 0630, New Zealand</li>
      </ul>
      <div class="web">www.<b>velmora</b>.co.nz</div>
      <div class="base-band"></div>
    </section>
  </main>
</body>
</html>
```